full stationary design for a modern sleek design company

we are a design company that does modern minimalistic interior design works as well as other design services for high end clients.
we need a full stationary design including and not limited to (double sided business card, letter head, envelopes, documents folder...etc) that reflects the modern style design we do.
sleek modern and minimalistic is the requirements.
Updates

please use the latest attached files as there was a slight modification on the logo Added Wednesday, March 1, 2017

minor update on the logo files in JPG and PSD has been updated kindly follow the new attachments. Added Thursday, March 2, 2017

Target Market(s)

modern minimalist clients

Industry/Entity Type

Design Agency

Requirements
Must have
• the logo
Nice to have
• i like the colors in the colored 3D logo attached
Should not have
• too many colors

```html
<!DOCTYPE html>
<html lang="en">
<head>
<meta charset="utf-8">
<title>Nordline Studio – Business Card</title>
<link rel="stylesheet" href="https://fonts.googleapis.com/css2?family=Open+Sans:wght@400;600&display=swap">
<style>
  :root {
    --backdrop: #ececec;
    --paper: #ffffff;
    --charcoal: #333536;
    --ink: #3a3a3a;
    --orange: #f7941d;
    --white: #ffffff;
  }
  * { box-sizing: border-box; margin: 0; padding: 0; }
  html, body {
    width: 1200px; height: 987px; overflow: hidden;
    background: var(--backdrop);
    font-family: "Open Sans", Arial, sans-serif;
  }
  .stage { position: relative; width: 1200px; height: 987px; }

  .card {
    position: absolute; left: 292px; width: 616px; height: 350px;
    overflow: hidden;
    box-shadow: 0 4px 14px rgba(0,0,0,0.18);
  }
  .card--front { top: 130px; background: var(--paper); border-radius: 0 47px 0 0; }
  .card--back  { top: 506px; background: var(--charcoal); border-radius: 47px 0 0 0; }

  .brand {
    position: absolute; display: flex; align-items: center; gap: 12px;
    font-weight: 600; font-size: 30px; letter-spacing: 2px; text-transform: uppercase;
    white-space: nowrap;
  }
  .brand__mark { width: 34px; height: 34px; background: var(--orange); flex: none; }
  .card--front .brand { left: 37px; top: 52px; color: var(--charcoal); }
  .card--back .brand { left: 50%; top: 156px; transform: translateX(-50%); color: var(--white); }

  .holder { position: absolute; right: 36px; top: 188px; text-align: right; }
  .holder__name { color: var(--orange); font-weight: 600; font-size: 21px; line-height: 26px; }
  .holder__role { color: var(--ink); font-size: 16px; line-height: 20px; }

  .divider {
    position: absolute; left: 173px; right: 36px; top: 246px;
    height: 1px; background: var(--ink);
  }

  .contacts { position: absolute; left: 32px; top: 234px; list-style: none; }
  .contacts li {
    display: flex; align-items: center; gap: 8px;
    font-size: 16px; line-height: 24px; color: var(--ink);
  }
  .contacts svg { width: 14px; height: 14px; fill: var(--orange); flex: none; }

  .address {
    position: absolute; right: 36px; top: 258px; text-align: right;
    font-size: 16px; line-height: 24px; color: var(--ink);
  }

  .base-band {
    position: absolute; left: 0; bottom: 0; width: 345px; height: 11px;
    background: var(--charcoal);
  }
  .base-band__gap { position: absolute; left: 16px; top: 0; width: 3px; height: 11px; background: var(--paper); }

  .web-tab {
    position: absolute; right: 0; bottom: 0; width: 275px; height: 33px;
    background: var(--orange); border-radius: 14px 0 0 0;
    color: var(--white); font-size: 15px; letter-spacing: 2px;
    display: flex; align-items: center; justify-content: center;
  }
</style>
</head>
<body>
<main class="stage">
  <section class="card card--front" aria-label="Business card front">
    <div class="brand"><span class="brand__mark"></span>Nordline Studio</div>

    <div class="holder">
      <p class="holder__name">ADAM KELLER</p>
      <p class="holder__role">CEO&amp;Founder</p>
    </div>

    <div class="divider"></div>

    <ul class="contacts">
      <li>
        <svg viewBox="0 0 24 24" aria-hidden="true"><path d="M6.6 10.8a15.1 15.1 0 0 0 6.6 6.6l2.2-2.2c.3-.3.7-.4 1-.2 1.1.4 2.3.6 3.6.6.6 0 1 .4 1 1V20c0 .6-.4 1-1 1A17 17 0 0 1 3 4c0-.6.4-1 1-1h3.5c.6 0 1 .4 1 1 0 1.3.2 2.5.6 3.6.1.3 0 .7-.2 1z"/></svg>
        (555) 210 4871
      </li>
      <li>
        <svg viewBox="0 0 24 24" aria-hidden="true"><path d="M7 1h10a2 2 0 0 1 2 2v18a2 2 0 0 1-2 2H7a2 2 0 0 1-2-2V3a2 2 0 0 1 2-2zm0 3v14h10V4zm5 15.5a1 1 0 1 0 0 2 1 1 0 0 0 0-2z"/></svg>
        (555) 382 6019
      </li>
      <li>
        <svg viewBox="0 0 24 24" aria-hidden="true"><path d="M2 5h20v14H2zm2 2v.4l8 5 8-5V7zm0 2.8V17h16V9.8l-8 5z"/></svg>
        adam@nordlinestudio.com
      </li>
    </ul>

    <address class="address" style="font-style:normal">
      1420 Harbor View Road<br>
      Portland, Maine 04101
    </address>

    <div class="base-band"><span class="base-band__gap"></span></div>
    <div class="web-tab">www.nordlinestudio.com</div>
  </section>

  <section class="card card--back" aria-label="Business card back">
    <div class="brand"><span class="brand__mark"></span>Nordline Studio</div>
  </section>
</main>
</body>
</html>
```